I need a sophisticated and powerful book cover design that combines Japanese minimalism with contemporary appeal. The cover should convey personal transformation through the metaphor of a katana (Japanese sword).
Key Design Elements:
A katana, either partially shown or artistically rendered
Subtle Japanese design elements without being stereotypical
Clean, minimalist aesthetic
Professional font selection that bridges Eastern and Western typography
Color scheme: Deep blacks, steel grays, and possibly a touch of red or gold for accent
Mood/Style:
Professional and sophisticated
Blend of traditional Japanese aesthetics with modern design
Should appeal to personal development and business readers
Must convey strength and transformation
Elegant rather than aggressive
Specific Requirements:
Title: "The Lantern Compass"
Subtitle: "Quiet Methods for Growing Inner Steadiness and Calm Endurance"
Author names: Dorvelan Thaske and Meloda Thaske
Cover dimensions: Standard hardcover book size (6" x 9")
Must work well in both physical and digital thumbnail formats
Should be striking and legible when viewed as a small image online
Design Specifics:
Japanese elements such as brushstroke effects, kanji characters, or wave patterns
The design should reflect the book's core message: personal transformation through Japanese wisdom principles, using the katana as a metaphor for growth and development.

```html
<!DOCTYPE html>
<html lang="en">
<head>
<meta charset="utf-8">
<title>The Lantern Compass — Book Cover</title>
<link rel="stylesheet" href="https://fonts.googleapis.com/css2?family=Cinzel:wght@400;500&display=swap">
<style>
  :root {
    --page: #ffffff;
    --cover-black: #020202;
    --ink-white: #f7f7f5;
    --steel-light: #e9ebec;
    --steel-mid: #9a9ea2;
    --steel-dark: #3a3c3f;
    --smoke: #1a1a1a;
  }
  * { margin: 0; padding: 0; box-sizing: border-box; }
  html, body {
    width: 1200px;
    height: 1200px;
    overflow: hidden;
    background: var(--page);
  }
  .canvas {
    position: relative;
    width: 1200px;
    height: 1200px;
    background: var(--page);
  }
  .cover {
    position: absolute;
    left: 235px;
    top: 53px;
    width: 730px;
    height: 1094px;
    background: radial-gradient(ellipse at 55% 60%, var(--smoke) 0%, var(--cover-black) 55%);
    overflow: hidden;
    font-family: "Cinzel", "Trajan Pro", serif;
    color: var(--ink-white);
  }
  .cover-art {
    position: absolute;
    inset: 0;
    width: 730px;
    height: 1094px;
  }
  .title {
    position: absolute;
    left: 48px;
    top: 58px;
    font-weight: 400;
    line-height: 1;
    letter-spacing: 1px;
  }
  .title-line {
    display: block;
    white-space: nowrap;
  }
  .title-line--first { font-size: 94px; }
  .title-line--second { font-size: 112px; margin-top: 12px; }
  .subtitle {
    position: absolute;
    left: 49px;
    top: 286px;
    width: 520px;
    font-size: 25px;
    line-height: 38px;
    font-weight: 400;
    letter-spacing: 1.2px;
  }
  .authors {
    position: absolute;
    right: 50px;
    top: 1030px;
    font-size: 27px;
    font-weight: 400;
    letter-spacing: 1px;
    white-space: nowrap;
  }
</style>
</head>
<body>
  <main class="canvas">
    <section class="cover">
      <svg class="cover-art" viewBox="0 0 730 1094" role="img" aria-label="Illustration of a polished katana laid diagonally from lower left to upper right, blade flecked with red, wrapped black hilt with gold guard, faint smoke swirling behind">
        <defs>
          <linearGradient id="steel" x1="0" y1="0" x2="0" y2="1">
            <stop offset="0" stop-color="var(--steel-light)"/>
            <stop offset="0.55" stop-color="var(--steel-mid)"/>
            <stop offset="1" stop-color="var(--steel-dark)"/>
          </linearGradient>
        </defs>
        <g transform="translate(367 625) rotate(-54.4)">
          <rect x="-533" y="-24" width="1066" height="48" rx="20" fill="url(#steel)"/>
        </g>
      </svg>

      <h1 class="title">
        <span class="title-line title-line--first">The Lantern</span>
        <span class="title-line title-line--second">Compass</span>
      </h1>

      <p class="subtitle">Quiet Methods for Growing Inner Steadiness and Calm Endurance</p>

      <p class="authors">Dorvelan Thaske and Meloda Thaske</p>
    </section>
  </main>
</body>
</html>
```